Business Card for Coastal Tundrabridge Advisory

We need a business card for Coastal Tundrabridge Advisory. The company website address is provided below. The company logo is attached. We provide specialized permafrost services to the mining, transportation, and oil & gas industries. The card should be prepared for:
Matthias Korhonen, PhD.
Coastal Tundrabridge Advisory
PO Box 418259
Quillwater, Alaska 99642
Direct: +1-907-555-0143
Email: mkorhonen@tundrabridgeadvisory.example
Website: www.coastaltundrabridgeadvisory.example

```html
<!DOCTYPE html>
<html lang="en">
<head>
<meta charset="utf-8">
<title>Coastal Tundrabridge Advisory — Business Card</title>
<link href="https://fonts.googleapis.com/css2?family=Roboto:wght@300;400;700&family=Roboto+Condensed:wght@400;700&display=swap" rel="stylesheet">
<style>
  :root {
    --backdrop: #2a2a2b;
    --card: #0f1520;
    --card-edge: #0a0e16;
    --ink: #ffffff;
    --ink-soft: #d9dde3;
    --ice-blue: #3fa9dd;
    --pattern-dark: #141c29;
  }
  * { margin: 0; padding: 0; box-sizing: border-box; }
  html, body { width: 1200px; height: 780px; overflow: hidden; background: var(--backdrop); }
  body { font-family: "Roboto", Arial, sans-serif; color: var(--ink); position: relative; }

  .card {
    position: absolute;
    top: 240px;
    width: 540px;
    height: 309px;
    background: var(--card);
    border-radius: 3px;
    box-shadow: 0 18px 40px rgba(0,0,0,.55);
    overflow: hidden;
  }
  .card--front { left: 40px; }
  .card--back { left: 620px; }

  /* Front */
  .holder { position: absolute; top: 26px; left: 0; padding-left: 22px; }
  .holder::before {
    content: ""; position: absolute; left: 0; top: 2px;
    width: 10px; height: 44px; background: var(--ink);
  }
  .holder__name { font-size: 27px; line-height: 1.05; letter-spacing: .2px; }
  .holder__first { font-weight: 700; }
  .holder__last { font-weight: 300; }
  .holder__title { font-size: 15px; font-weight: 400; margin-top: 1px; }

  .wordmark { position: absolute; font-family: "Roboto", Arial, sans-serif; font-weight: 700; color: var(--ink); display: flex; align-items: center; gap: 8px; }
  .wordmark__square { width: 12px; height: 12px; background: var(--ink); flex: none; }
  .card--front .wordmark { right: 34px; top: 122px; font-size: 21px; }

  .address { position: absolute; left: 26px; bottom: 30px; font-size: 12.5px; line-height: 1.5; color: var(--ink-soft); font-weight: 300; }

  .contact { position: absolute; right: 24px; bottom: 24px; list-style: none; text-align: right; font-size: 12.5px; line-height: 1.55; color: var(--ink-soft); }
  .contact li { display: flex; justify-content: flex-end; align-items: center; gap: 7px; }
  .contact svg { width: 13px; height: 13px; flex: none; }

  /* Back */
  .back-texture {
    position: absolute; inset: 0;
    background: linear-gradient(110deg, var(--pattern-dark) 0%, #142133 45%, #1c4a6e 75%, var(--ice-blue) 100%);
    opacity: .9;
  }
  .card--back .wordmark { left: 50%; top: 112px; transform: translateX(-50%); font-size: 24px; white-space: nowrap; }
  .services { position: absolute; left: 24px; right: 24px; bottom: 30px; text-align: center; font-family: "Roboto Condensed", Arial, sans-serif; }
  .services__heading { font-size: 12px; font-weight: 700; letter-spacing: .5px; margin-bottom: 4px; }
  .services__text { font-size: 11.5px; font-style: italic; font-weight: 400; color: var(--ink-soft); }
</style>
</head>
<body>

<section class="card card--front" aria-label="Business card front">
  <div class="holder">
    <p class="holder__name"><span class="holder__first">Matthias</span> <span class="holder__last">Korhonen</span></p>
    <p class="holder__title">PhD</p>
  </div>

  <div class="wordmark"><span class="wordmark__square"></span>Coastal Tundrabridge Advisory</div>

  <address class="address">
    PO Box 418259<br>
    Quillwater, Alaska 99642
  </address>

  <ul class="contact">
    <li>+1-907-555-0143
      <svg viewBox="0 0 16 16" aria-hidden="true"><circle cx="8" cy="8" r="8" fill="#fff"/><path d="M5.2 3.8l1.6 1.8-.8 1.2c.6 1.3 1.6 2.3 2.9 2.9l1.2-.8 1.8 1.6-.9 1.5C8.2 11.8 4.2 7.8 4 5z" fill="#0f1520"/></svg>
    </li>
    <li>mkorhonen@tundrabridgeadvisory.example
      <svg viewBox="0 0 16 16" aria-hidden="true"><circle cx="8" cy="8" r="8" fill="#fff"/><rect x="3.5" y="5" width="9" height="6.2" fill="none" stroke="#0f1520" stroke-width="1.2"/><path d="M3.5 5l4.5 3.6L12.5 5" fill="none" stroke="#0f1520" stroke-width="1.2"/></svg>
    </li>
    <li>www.coastaltundrabridgeadvisory.example
      <svg viewBox="0 0 16 16" aria-hidden="true"><circle cx="8" cy="8" r="8" fill="#fff"/><circle cx="8" cy="8" r="4.8" fill="none" stroke="#0f1520" stroke-width="1"/><ellipse cx="8" cy="8" rx="2" ry="4.8" fill="none" stroke="#0f1520" stroke-width="1"/><path d="M3.2 8h9.6" stroke="#0f1520" stroke-width="1"/></svg>
    </li>
  </ul>
</section>

<section class="card card--back" aria-label="Business card back">
  <div class="back-texture" role="img" aria-label="Repeating company-name texture fading from dark navy to ice blue"></div>

  <div class="wordmark"><span class="wordmark__square"></span>Coastal Tundrabridge Advisory</div>

  <div class="services">
    <p class="services__heading">OUR SERVICES</p>
    <p class="services__text">We provide specialized permafrost services to the mining, transportation, and oil &amp; gas industries</p>
  </div>
</section>

</body>
</html>
```